Business Card Design Project - del varosi group

dear Sirs

we need business card design for our group ( DEL Varosi Group ) , i have got the Logo design of our group from pixel harbor in previous , so all need details relating to our group i think available with you, as well as the the chosen logo design

we hope to provide us with business card logo that to be appropaite and satisfactory to us .

thanks

note : logo design of our group is attached .
Updates

Reason: please extend the deadline of my project for additional 15 days because i didn't received appropriate design for our gruop yet . kindly beaware that i have received 77 design till now , supossed to send me 200-250 design at least . thanks

Target Market(s)

contents

name : Kerem EL Nadiri

position : Operation Manager

Industry/Entity Type

Business

Requirements
Must have

• person name

group logo
Nice to have
• logo color matching with back background

```html
<!DOCTYPE html>
<html lang="en">
<head>
<meta charset="utf-8">
<title>DEL Varosi Group – Business Card</title>
<link rel="stylesheet" href="https://fonts.googleapis.com/css2?family=Lato:wght@400;700&display=swap">
<style>
  :root {
    --backdrop: #e6e2dc;
    --card-white: #f7f7f5;
    --card-black: #141414;
    --brand-blue: #1565b4;
    --ink: #1e1e1e;
    --ink-soft: #333333;
    --rule: #2a2a2a;
  }
  * { margin: 0; padding: 0; box-sizing: border-box; }
  html, body { width: 1200px; height: 720px; overflow: hidden; }
  body {
    background: var(--backdrop);
    font-family: "Lato", sans-serif;
    color: var(--ink);
    position: relative;
  }
  .card {
    position: absolute;
    top: 212px;
    width: 520px;
    height: 297px;
    box-shadow: 0 6px 18px rgba(0,0,0,0.18);
  }
  .card--front { left: 50px; background: var(--card-white); }
  .card--back  { left: 630px; background: var(--card-black); }

  .brand-name {
    font-family: "Lato", sans-serif;
    font-weight: 700;
    color: var(--brand-blue);
    letter-spacing: 0.5px;
    white-space: nowrap;
    display: flex;
    align-items: center;
    gap: 10px;
  }
  .brand-name__square {
    width: 14px; height: 14px;
    background: var(--brand-blue);
    flex: none;
  }
  .card--front .brand-name { position: absolute; left: 30px; top: 30px; font-size: 24px; }
  .card--back .brand-name {
    position: absolute; left: 0; right: 0; top: 128px;
    justify-content: center; font-size: 34px;
  }
  .card--back .brand-name__square { width: 20px; height: 20px; }

  .rule-top {
    position: absolute; left: 30px; right: 30px; top: 92px;
    height: 1px; background: var(--rule);
  }
  .person { position: absolute; left: 30px; top: 108px; }
  .person__name { font-size: 21px; font-weight: 400; color: var(--ink); }
  .person__role { font-size: 13px; color: var(--ink-soft); margin-top: 3px; }
  .rule-person {
    position: absolute; left: 30px; top: 166px;
    width: 180px; height: 1px; background: var(--rule);
  }
  .contacts {
    position: absolute; left: 30px; top: 180px;
    list-style: none; font-size: 13.5px; color: var(--ink);
  }
  .contacts li { display: flex; align-items: center; gap: 12px; height: 20px; }
  .contacts svg { width: 13px; height: 13px; flex: none; fill: var(--brand-blue); }
  .address {
    position: absolute; right: 30px; top: 108px;
    text-align: right; font-size: 13px; line-height: 1.4; color: var(--ink);
  }
  .address__web { font-weight: 700; }
</style>
</head>
<body>
  <section class="card card--front" aria-label="Business card front">
    <div class="brand-name"><span class="brand-name__square"></span>DEL VAROSI GROUP</div>
    <div class="rule-top"></div>
    <div class="person">
      <p class="person__name">Kerem EL Nadiri</p>
      <p class="person__role">Operation Manager</p>
    </div>
    <div class="rule-person"></div>
    <ul class="contacts">
      <li>
        <svg viewBox="0 0 16 16" aria-hidden="true"><rect x="1" y="1" width="14" height="14" rx="2"/><rect x="4" y="3" width="4" height="10" fill="#f7f7f5"/><rect x="10" y="4" width="3" height="2" fill="#f7f7f5"/><rect x="10" y="8" width="3" height="2" fill="#f7f7f5"/></svg>
        (221) 33 410 22 58
      </li>
      <li>
        <svg viewBox="0 0 16 16" aria-hidden="true"><rect x="4" y="1" width="8" height="5"/><rect x="1" y="6" width="14" height="6" rx="1"/><rect x="4" y="11" width="8" height="4"/></svg>
        (221) 33 417 64 30
      </li>
      <li>
        <svg viewBox="0 0 16 16" aria-hidden="true"><rect x="4" y="0.5" width="8" height="15" rx="1.5"/><rect x="5.5" y="2.5" width="5" height="8" fill="#f7f7f5"/></svg>
        (221) 77 502 18 46
      </li>
      <li>
        <svg viewBox="0 0 16 16" aria-hidden="true"><path d="M1 3h14v10H1z M2.5 4.5v7h11v-7L8 9z" fill-rule="evenodd"/></svg>
        kerem-nadiri@del-varosi.com
      </li>
    </ul>
    <address class="address" style="font-style: normal;">
      Avenue des Palmiers - Port Nord<br>
      BP 512 - Corvane, Sénégal<br>
      <span class="address__web">www.del-varosi.com</span>
    </address>
  </section>

  <section class="card card--back" aria-label="Business card back">
    <div class="brand-name"><span class="brand-name__square"></span>DEL VAROSI GROUP</div>
  </section>
</body>
</html>
```